develop our online residential property development appraisal service

This project requires a detailed WordPress design to represent a new digital residential property development consultancy business. At its heart it will have a number of different products that essentially advise customers of the potential value and feasibility of developing their residential site into multiple townhouses, units, apartments, etc... This will be accompanied by explaining the considerations of residential property development.

We aim to navigate and break down this complex area and provide our customers with the tools, knowledge, control and power to 'unlock the value' in their property.

REFERENCE DOCUMENTS:
1. Detailed solution requirements please refer to the attached 'wordpressdesignrequirements'
2. Logo files, style guide and colour pallet please refer to the attached 'KRLM.zip'
3. Site Map refer to attached 'wordpressdesignsitemap'

Reason: Additional information provided so extending period for designs to take into account.

Target Market(s)

The site will appeal to professional service providers; accountants, financial planners, lawyers, etc…

Industry/Entity Type

Residential

Font styles to use
Sans Serif
Other font styles liked:
• Similar to the logo font, slim line and simple

Requirements
Must have
• The logo, style and colour palette provided in the attached 'KRLM.zip' files
• Satisfy the intent of the 'wordpressdesignrequirements'
• Present as an online-centric business
• Clean, crisp and modern design
• Predominant use of white as a background contrasted with the colours provided in the colour palette
Nice to have
• Use of the following WordPress business themes is encouraged but not mandatory:
• 1. Mavo
• 2. Tulek
• 3. Vupa
Should not have
• Overt references to Australia

```html
<!DOCTYPE html>
<html lang="en">
<head>
<meta charset="utf-8">
<title>KRLM – Residential Development Appraisals</title>
<link rel="stylesheet" href="https://fonts.googleapis.com/css2?family=Arimo:wght@400;700&display=swap">
<style>
:root{
  --topbar:#1b9ccf;
  --teal:#27a59b;
  --teal-dark:#1f948b;
  --teal-light:#3cbcb0;
  --blue-box:#1a9fd9;
  --mint:#8dd2bc;
  --footer:#1a9dbd;
  --footer-line:#5cc0d6;
  --text:#555;
  --brand-text:#4a4a4a;
  --muted:#8a8a8a;
  --white:#fff;
  --field:#e6e6e6;
}
*{margin:0;padding:0;box-sizing:border-box}
html,body{width:791px;height:1200px;overflow:hidden;background:var(--white)}
body{font-family:"Arimo",Arial,sans-serif;color:var(--text);position:relative}
ul{list-style:none}
.abs{position:absolute}

/* top bar */
.topbar{position:absolute;left:0;top:0;width:791px;height:22px;background:var(--topbar);color:var(--white);font-size:7px}
.topbar .email{position:absolute;left:108px;top:7px;display:flex;align-items:center;gap:5px}
.topbar .login{position:absolute;left:499px;top:8px}
.topbar .social{position:absolute;left:560px;top:0;display:flex}
.topbar .social span{width:25px;height:22px;border-left:1px solid rgba(255,255,255,.35);display:flex;align-items:center;justify-content:center}
.topbar .social span i{width:6px;height:6px;border-radius:50%;background:var(--white);display:block}

/* header */
.brand{position:absolute;left:118px;top:44px;display:flex;align-items:center;gap:7px;font-size:15px;font-weight:700;color:var(--brand-text)}
.brand .mark{width:14px;height:14px;background:var(--teal);display:block}
.search{position:absolute;left:499px;top:36px;width:185px;height:19px;background:var(--field);font-size:8px;color:#999;padding:5px 6px}
.search svg{position:absolute;right:6px;top:4px}
.nav{position:absolute;left:393px;top:60px;display:flex;font-size:7px;color:#666}
.nav a{display:block;height:23px;line-height:23px;padding:0 7px;margin-right:6px;color:inherit;text-decoration:none}
.nav a.active{background:var(--teal);color:var(--white);padding:0 8px}

/* hero */
.hero{position:absolute;left:0;top:83px;width:791px;height:219px;background:linear-gradient(180deg,#7a6f7c 0%,#b49a8b 35%,#8b8a76 65%,#566a44 100%)}
.hero-card{position:absolute;left:105px;top:69px;width:242px;height:73px;background:rgba(62,186,128,.85);color:var(--white);padding:11px 12px}
.hero-card h1{font-size:13px;font-weight:400;margin-bottom:6px}
.hero-card p{font-size:7.5px;line-height:13px}
.btn{display:inline-block;background:var(--teal);color:var(--white);font-size:7px;padding:4px 5px}
.hero .btn{position:absolute;left:105px;top:144px;background:var(--teal-dark)}

.section-title{font-size:13px;font-weight:400;color:var(--teal)}

/* know about */
.tabs{position:absolute;left:104px;top:351px;width:379px;height:30px;background:var(--teal);font-size:7.5px;color:var(--white)}
.tabs svg{position:absolute;left:0;top:0}
.tabs span{position:absolute;top:11px}
.tabs .current{border-bottom:1px solid var(--white);padding-bottom:3px}
.about-box{position:absolute;left:104px;top:381px;width:379px;height:179px;background:var(--blue-box)}
.about-box p{position:absolute;left:202px;top:13px;width:168px;font-size:7.5px;line-height:15px;color:var(--white)}
.about-box .btn{position:absolute;left:205px;top:141px}

.opps{position:absolute;left:504px;top:324px;width:180px}
.opps li{position:relative;padding-left:11px;font-size:7.5px;line-height:12px;color:var(--muted);margin-bottom:12px}
.opps li svg{position:absolute;left:0;top:2px}

/* recent */
.recent{position:absolute;left:0;top:585px;width:791px;height:178px;background:var(--mint)}
.recent .photo{position:absolute;left:112px;top:15px;width:274px;height:148px;background:linear-gradient(180deg,#9dc1e2 0%,#d8dad8 45%,#8a8174 80%,#6b6a56 100%)}
.recent .copy{position:absolute;left:403px;top:14px;width:262px;color:var(--white)}
.recent h3{font-size:11px;font-weight:400;color:#444;margin:10px 0 8px}
.recent p{font-size:7.5px;line-height:13.5px}
.recent .btn{margin-top:8px}

/* reports */
.report{position:absolute;top:812px;width:179px}
.report .photo{height:127px}
.report .row{display:flex;justify-content:space-between;align-items:center;margin-top:6px}
.report .title{font-size:10px;color:#333}
.report .btn{font-size:8px;padding:5px 5px}
.pager{position:absolute;left:380px;top:978px;display:flex;gap:4px}
.pager span{width:12px;height:12px;display:flex;align-items:center;justify-content:center}

/* footer */
.footer{position:absolute;left:0;top:1016px;width:791px;height:184px;background:var(--footer);color:var(--white)}
.footer h4{font-size:10px;font-weight:400;margin-bottom:8px}
.footer .col{position:absolute;top:25px}
.footer li{font-size:7.5px;margin-bottom:7px;display:flex;align-items:center;gap:6px}
.footer .circles{display:flex;gap:6px;margin-top:14px}
.footer .circles i{width:14px;height:14px;border:1px solid var(--white);border-radius:50%;display:block}
.footer .email-field{width:128px;height:17px;background:#15879f;font-size:7px;padding:5px;position:relative;margin-bottom:14px}
.footer .email-field svg{position:absolute;right:4px;top:4px}
.footer .bottom{position:absolute;left:105px;top:156px;width:580px;border-top:1px solid var(--footer-line);padding-top:8px;font-size:7px}
</style>
</head>
<body>

<header>
  <div class="topbar">
    <div class="email">
      <svg width="7" height="6" viewBox="0 0 7 6"><rect width="7" height="6" rx="1" fill="#fff"/><path d="M0 1l3.5 2.5L7 1" stroke="#1b9ccf" fill="none" stroke-width=".8"/></svg>
      hello@kestrelappraisals.com
    </div>
    <div class="login">&#8594; Login / Register</div>
    <div class="social"><span><i></i></span><span><i></i></span><span><i></i></span><span><i></i></span><span><i></i></span></div>
  </div>

  <div class="brand"><span class="mark"></span>KRLM Residential Appraisals</div>

  <div class="search">Search...
    <svg width="10" height="10" viewBox="0 0 10 10"><circle cx="4" cy="4" r="3" stroke="#999" stroke-width="1.3" fill="none"/><path d="M6.3 6.3L9 9" stroke="#999" stroke-width="1.5"/></svg>
  </div>

  <nav class="nav">
    <a class="active" href="#">Home</a><a href="#">About Us</a><a href="#">Property Report</a><a href="#">Property Development</a><a href="#">Contact Us</a>
  </nav>
</header>

<section class="hero" role="img" aria-label="Modern two-storey white house at dusk with lit windows and garden">
  <div class="hero-card">
    <h1>Necessitatibus Saepe Eveniet</h1>
    <p>At vero eos et accusamus et iusto odio dignissimos ducimus qui blanditiis praesentium voluptatum...</p>
  </div>
  <span class="btn">Know More &#187;</span>
</section>

<section class="know">
  <h2 class="section-title abs" style="left:116px;top:324px">Know About US</h2>
  <div class="tabs">
    <svg width="379" height="30" viewBox="0 0 379 30">
      <path d="M69 30L80 0H143L132 30Z" fill="var(--teal-light)"/>
      <path d="M143 0L132 30" stroke="#fff" stroke-width=".8"/>
      <path d="M229 0L218 30" stroke="#fff" stroke-width=".8"/>
    </svg>
    <span class="current" style="left:74px">WHO are we?</span>
    <span style="left:148px">WHAT do we do?</span>
    <span style="left:237px">HOW do we do it?</span>
  </div>
  <div class="about-box">
    <div class="abs" role="img" aria-label="Two-storey suburban home with red flowering garden" style="left:8px;top:15px;width:177px;height:150px;background:linear-gradient(180deg,#7fb3e6 0%,#cfd6dc 40%,#9a8c7c 65%,#8a7b5e 100%)"></div>
    <p>Kestrel Residential Appraisals is a digital residential property development consultancy business. At its heart it will have a number of different products that essentially advise customers of the potential value and feasibility of developing their residential site into multiple townhouses, units, apartments, etc...</p>
    <span class="btn">Know More &#187;</span>
  </div>
</section>

<aside class="opps">
  <h2 class="section-title" style="margin-bottom:12px">Opportunities</h2>
  <ul>
    <li><svg width="6" height="7" viewBox="0 0 6 7"><path d="M3 0L6 3V7H0V3Z" fill="#27a59b"/></svg>Sed quia non numquam eius dolor sit amet, consectetur.</li>
    <li><svg width="6" height="7" viewBox="0 0 6 7"><path d="M3 0L6 3V7H0V3Z" fill="#27a59b"/></svg>Labore et dolore laboris nisi ut aliquip ex ea commodo consequat.</li>
    <li><svg width="6" height="7" viewBox="0 0 6 7"><path d="M3 0L6 3V7H0V3Z" fill="#27a59b"/></svg>Corporis suscipit laboriosa messe cillum dolore eu fugiat nulla.</li>
    <li><svg width="6" height="7" viewBox="0 0 6 7"><path d="M3 0L6 3V7H0V3Z" fill="#27a59b"/></svg>Similique sunt in culpa et quasi architecto beatae vitae dicta sunt explicabo.</li>
    <li><svg width="6" height="7" viewBox="0 0 6 7"><path d="M3 0L6 3V7H0V3Z" fill="#27a59b"/></svg>Quod maxime plac consequuntur magni dolores eos qui ratione.</li>
    <li><svg width="6" height="7" viewBox="0 0 6 7"><path d="M3 0L6 3V7H0V3Z" fill="#27a59b"/></svg>Ta sunt explicabo nemo enim ipsam volu ptatem quia voluptas sitqui.</li>
  </ul>
</aside>

<section class="recent">
  <div class="photo" role="img" aria-label="Contemporary white house with stone wall and front steps"></div>
  <div class="copy">
    <h2 class="section-title" style="color:var(--teal)">Recent Property Development</h2>
    <h3>Soluta Nobis Est</h3>
    <p>Temporibus autem quibusdam et aut officiis debitis aut rerum necess itatibus saepe eveniet.Neque porro quisquam est, qui dolorem ipsum quia dolor sit amet, consectetur, adipisci velit, sedm nisi ut aliquid ex ea commodi consequatur? Quis autem vel eum iure reprehenderit qui in ea voluptate velit esse quam nihil molestiae consequatur, vel illum qui dolorem eum fugiat quo voluptas nulla pariatur...</p>
    <span class="btn">Know More &#187;</span>
  </div>
</section>

<section class="reports">
  <h2 class="section-title abs" style="left:116px;top:786px">Property Report Summary</h2>
  <div class="report" style="left:111px">
    <div class="photo" role="img" aria-label="Period cottage with front garden path" style="background:linear-gradient(180deg,#b9d3ea 0%,#9eab86 45%,#5f8a3e 100%)"></div>
    <div class="row"><span class="title">Property Report A</span><span class="btn">Request Report</span></div>
  </div>
  <div class="report" style="left:306px">
    <div class="photo" role="img" aria-label="Modern white house with timber garage door" style="background:linear-gradient(180deg,#9ac1e4 0%,#e3e3e0 40%,#7c6a55 75%,#4f5a3a 100%)"></div>
    <div class="row"><span class="title">Property Report B</span><span class="btn">Request Report</span></div>
  </div>
  <div class="report" style="left:500px">
    <div class="photo" role="img" aria-label="Timber-clad two-storey home with balcony" style="background:linear-gradient(180deg,#6fa6dc 0%,#d6d4cf 45%,#9a7a5a 75%,#5c7a3a 100%)"></div>
    <div class="row"><span class="title">Property Report C</span><span class="btn">Request Report</span></div>
  </div>
  <div class="pager">
    <span style="background:#4caf50"><svg width="5" height="6" viewBox="0 0 5 6"><path d="M5 0V6L0 3Z" fill="#fff"/></svg></span>
    <span style="background:#ddd"><svg width="5" height="6" viewBox="0 0 5 6"><path d="M0 0V6L5 3Z" fill="#fff"/></svg></span>
  </div>
</section>

<footer class="footer">
  <div class="col" style="left:117px">
    <h4>About Us</h4>
    <ul><li>&#8250; WHO we are?</li><li>&#8250; WHAT do we do?</li><li>&#8250; HOW do we do it?</li></ul>
    <div class="circles"><i></i><i></i><i></i><i></i><i></i></div>
  </div>
  <div class="col" style="left:309px">
    <h4>Links</h4>
    <ul><li>&#8250; About US</li><li>&#8250; Opportunities</li><li>&#8250; Property Report</li><li>&#8250; Property Development</li><li>&#8250; Contact Us</li><li>&#8250; Site Map</li></ul>
  </div>
  <div class="col" style="left:503px">
    <h4>Search</h4>
    <div class="email-field">Enter your email ...
      <svg width="10" height="10" viewBox="0 0 10 10"><circle cx="4" cy="4" r="3" stroke="#fff" stroke-width="1.3" fill="none"/><path d="M6.3 6.3L9 9" stroke="#fff" stroke-width="1.5"/></svg>
    </div>
    <h4>Contact&nbsp; Us</h4>
    <ul>
      <li><svg width="7" height="6" viewBox="0 0 7 6"><rect width="7" height="6" rx="1" fill="#fff"/><path d="M0 1l3.5 2.5L7 1" stroke="#1a9dbd" fill="none" stroke-width=".8"/></svg>hello@kestrelappraisals.com</li>
      <li><svg width="6" height="7" viewBox="0 0 6 7"><path d="M1 0h1.5l.5 2-1 1c.5 1 1 1.5 2 2l1-1 1 .5V7C3 7 0 4 1 0Z" fill="#fff"/></svg>0-000-000-0000</li>
    </ul>
  </div>
  <div class="bottom">&#169; Copyright information here</div>
</footer>

</body>
</html>
```